Business Card Design Project

Business card based on attached logo

Todd Merrick
Todd@lorvantest.com
877-514-9073 ext. 318
Www.LorvanTest.com

Industry/Entity Type

Business

```html
<!DOCTYPE html>
<html lang="en">
<head>
<meta charset="utf-8">
<title>LorvanTest Business Cards</title>
<link href="https://fonts.googleapis.com/css2?family=Archivo:wght@400;600;800&display=swap" rel="stylesheet">
<style>
  :root{
    --backdrop:#5e3522;
    --paper:#ffffff;
    --brand-red:#e81c24;
    --ink:#231f20;
    --ink-soft:#3a3a3a;
    --rule:#c9c9c9;
  }
  *{margin:0;padding:0;box-sizing:border-box}
  html,body{width:1200px;height:715px;overflow:hidden}
  body{background:var(--backdrop);font-family:"Archivo",Arial,sans-serif;position:relative}

  .card{position:absolute;width:505px;height:290px;border-radius:20px;overflow:hidden}
  .card--contact{left:54px;top:46px;background:var(--paper)}
  .card--white{left:623px;top:37px;background:var(--paper)}
  .card--red{left:51px;top:379px;background:var(--brand-red)}
  .card--black{left:629px;top:380px;background:var(--ink)}

  .brand{display:flex;align-items:center;gap:10px;font-weight:800;line-height:1;letter-spacing:-1px}
  .brand__mark{display:block;background:var(--brand-red)}
  .brand--small{position:absolute;left:52px;top:96px;font-size:36px;color:var(--ink)}
  .brand--small .brand__mark{width:14px;height:14px}
  .brand--large{position:absolute;left:0;right:0;top:92px;justify-content:center;font-size:66px}
  .brand--large .brand__mark{width:22px;height:22px}
  .card--white .brand--large{color:var(--ink)}
  .card--red .brand--large,.card--black .brand--large{color:var(--paper)}
  .card--red .brand__mark,.card--black .brand__mark{background:var(--paper)}

  .divider{position:absolute;left:287px;top:70px;width:1px;height:100px;background:var(--rule)}
  .contact-list{position:absolute;left:300px;top:66px;list-style:none;font-size:13px;color:var(--ink-soft)}
  .contact-list li{display:flex;align-items:center;gap:7px;height:34px}
  .contact-list svg{width:10px;height:10px;flex:none}

  .swoosh{position:absolute;left:0;bottom:0;width:505px;height:90px}
  .holder-name{position:absolute;left:50px;top:256px;font-size:18px;font-weight:600;letter-spacing:1px;color:var(--paper)}

  .web{position:absolute;left:0;right:0;bottom:18px;text-align:center;font-size:14px;letter-spacing:3px}
  .card--white .web{color:var(--ink)}
  .card--red .web,.card--black .web{color:var(--paper)}
</style>
</head>
<body>

<section class="card card--contact">
  <div class="brand brand--small">LorvanTest<span class="brand__mark"></span></div>
  <div class="divider"></div>
  <ul class="contact-list">
    <li><svg viewBox="0 0 10 10"><circle cx="5" cy="5" r="4.5" fill="none" stroke="#e81c24" stroke-width="1"/><path d="M3.3 2.8c.4 1.9 1.6 3.4 3.4 4.2" stroke="#e81c24" stroke-width="1.3" fill="none" stroke-linecap="round"/></svg>877-514-9073 ext. 318</li>
    <li><svg viewBox="0 0 10 10"><rect x="0.5" y="2" width="9" height="6.5" fill="#e81c24"/><path d="M0.5 2.5L5 6l4.5-3.5" stroke="#fff" stroke-width="0.9" fill="none"/></svg>Todd@lorvantest.com</li>
    <li><svg viewBox="0 0 10 10"><circle cx="5" cy="5" r="4.3" fill="none" stroke="#e81c24" stroke-width="1"/><ellipse cx="5" cy="5" rx="1.9" ry="4.3" fill="none" stroke="#e81c24" stroke-width="0.8"/><path d="M0.7 5h8.6" stroke="#e81c24" stroke-width="0.8"/></svg>www.LorvanTest.com</li>
  </ul>
  <svg class="swoosh" viewBox="0 0 505 90" preserveAspectRatio="none" aria-hidden="true">
    <path d="M0 42C120 0 220 10 330 44C410 68 465 70 505 58V90H0Z" fill="#231f20"/>
    <path d="M0 48C120 8 220 18 330 51C410 74 465 76 505 65V90H0Z" fill="#ffffff"/>
    <path d="M0 52C120 14 220 24 330 56C410 79 465 81 505 70V90H0Z" fill="#e81c24"/>
  </svg>
  <p class="holder-name">Todd Merrick</p>
</section>

<section class="card card--white">
  <div class="brand brand--large">LorvanTest<span class="brand__mark"></span></div>
  <p class="web">www.LorvanTest.com</p>
</section>

<section class="card card--red">
  <div class="brand brand--large">LorvanTest<span class="brand__mark"></span></div>
  <p class="web">www.LorvanTest.com</p>
</section>

<section class="card card--black">
  <div class="brand brand--large">LorvanTest<span class="brand__mark"></span></div>
  <p class="web">www.LorvanTest.com</p>
</section>

</body>
</html>
```